Brightway Haul & Upkeep Services, are a company that offers a 'one stop shop' pre-move clean up a

I have already selected a logo which I would like on the front of the business cards along with phone numbers, web address and email which are:
0487650392
www.brightwayhaul.com.au
brightwayhaulandupkeep@mailbox.example

On the back of the card I would like to list some of the types of service we offer (clean - move - repairs/maintenance) which are:
CLEAN - windows, gutters, solar panels, driveways/paths, carpets.
MOVE - Small/medium size house/office moves, large item pick-up & delivery, yard clean-up and removal.
General maintenance and repairs.

I would like the blue logo on a gray background.

Thanks

```html
<!DOCTYPE html>
<html lang="en">
<head>
<meta charset="utf-8">
<title>Brightway Haul &amp; Upkeep Services – Business Card</title>
<link rel="stylesheet" href="https://fonts.googleapis.com/css2?family=PT+Sans:wght@400;700&display=swap">
<style>
  :root {
    --stage: #e4e2df;
    --card-light: #f4f4f4;
    --card-mid: #c9cacc;
    --brand-blue: #2271bb;
    --ink: #1c1c1c;
    --white: #ffffff;
    --text-font: "PT Sans", sans-serif;
  }
  * { box-sizing: border-box; margin: 0; padding: 0; }
  html, body {
    width: 1200px; height: 682px; overflow: hidden;
    background: var(--stage);
    font-family: var(--text-font);
  }
  .stage {
    position: relative; width: 1200px; height: 682px;
    display: flex; align-items: center; justify-content: center; gap: 50px;
  }
  .card {
    position: relative; width: 520px; height: 298px; overflow: hidden;
    background: radial-gradient(ellipse at 45% 35%, var(--card-light) 0%, #e2e2e3 45%, var(--card-mid) 100%);
    box-shadow: 0 6px 18px rgba(0,0,0,0.25);
  }
  .brand {
    display: flex; align-items: center; gap: 12px;
    color: var(--brand-blue); font-weight: 700;
  }
  .brand-mark {
    width: 22px; height: 22px; background: var(--brand-blue); flex: none;
  }
  .brand-name { line-height: 1.05; }

  /* Front */
  .card-front .brand {
    position: absolute; left: 70px; top: 66px; width: 400px;
    font-size: 34px;
  }
  .card-front .band { position: absolute; left: 0; top: 0; }
  .contact {
    position: absolute; right: 40px; top: 206px; color: var(--white);
    font-size: 14px; display: flex; gap: 18px; align-items: center;
  }
  .contact-item { display: flex; align-items: center; gap: 5px; }
  .contact-item svg { flex: none; }
  .website {
    position: absolute; left: 150px; top: 248px; color: var(--white);
    font-size: 15px; font-weight: 700; letter-spacing: 4px;
  }

  /* Back */
  .card-back .brand {
    position: absolute; left: 34px; top: 26px; font-size: 26px; width: 460px;
  }
  .services { position: absolute; left: 34px; top: 120px; right: 30px; }
  .services-title {
    color: var(--brand-blue); font-size: 24px; font-weight: 400; letter-spacing: 2px;
    margin-bottom: 10px;
  }
  .service-row { display: flex; gap: 10px; font-size: 15px; color: var(--ink); margin-bottom: 6px; line-height: 1.25; }
  .service-label { color: var(--brand-blue); font-weight: 700; width: 54px; flex: none; }
  .service-general {
    color: var(--brand-blue); font-weight: 700; font-size: 17px; letter-spacing: 1.5px; margin-top: 6px;
  }
</style>
</head>
<body>
<main class="stage">
  <section class="card card-front" aria-label="Card front">
    <svg class="band" width="520" height="298" viewBox="0 0 520 298" aria-hidden="true">
      <path d="M0 222 C 120 180, 300 150, 520 150 L520 298 L0 298 Z" fill="var(--brand-blue)"/>
      <path d="M40 200 C 170 150, 330 138, 500 140 C 330 146, 170 166, 40 200 Z" fill="var(--ink)"/>
    </svg>
    <div class="brand">
      <span class="brand-mark"></span>
      <span class="brand-name">Brightway Haul &amp; Upkeep Services</span>
    </div>
    <div class="contact">
      <span class="contact-item">
        <svg width="12" height="12" viewBox="0 0 24 24" aria-hidden="true"><path fill="#fff" d="M6.6 10.8a15 15 0 0 0 6.6 6.6l2.2-2.2a1 1 0 0 1 1-.25 11.4 11.4 0 0 0 3.6.57 1 1 0 0 1 1 1V20a1 1 0 0 1-1 1A17 17 0 0 1 3 4a1 1 0 0 1 1-1h3.5a1 1 0 0 1 1 1c0 1.25.2 2.45.57 3.57a1 1 0 0 1-.25 1z"/></svg>
        0487650392
      </span>
      <span class="contact-item">
        <svg width="13" height="10" viewBox="0 0 26 20" aria-hidden="true"><rect x="1" y="1" width="24" height="18" rx="2" fill="#fff"/><path d="M2 3l11 8 11-8" fill="none" stroke="var(--brand-blue)" stroke-width="2"/></svg>
        brightwayhaulandupkeep@mailbox.example
      </span>
    </div>
    <div class="website">www.brightwayhaul.com.au</div>
  </section>

  <section class="card card-back" aria-label="Card back">
    <div class="brand">
      <span class="brand-mark"></span>
      <span class="brand-name">Brightway Haul &amp; Upkeep Services</span>
    </div>
    <div class="services">
      <h2 class="services-title">Services we offer</h2>
      <div class="service-row"><span class="service-label">CLEAN:</span><span>Windows, Gutters, Solar Panels, Driveways/paths, Carpets.</span></div>
      <div class="service-row"><span class="service-label">MOVE:</span><span>Small/medium Size House/office Moves, Large Item Pick-up &amp; Delivery, Yard Clean-up And Removal.</span></div>
      <p class="service-general">General maintenance and repairs.</p>
    </div>
  </section>
</main>
</body>
</html>
```